Vale Crest - Business Cards

We are a consultancy to help builders to optimize their planning in order to save building costs. For that reason we need a clean and professional business card for our high-priced services. A QR code should lead to the contact information needed.

```html
<!DOCTYPE html>
<html lang="en">
<head>
<meta charset="utf-8">
<title>Vale Crest - Business Cards</title>
<link rel="stylesheet" href="https://fonts.googleapis.com/css2?family=Roboto:wght@400;500;700&display=swap">
<style>
  :root {
    --backdrop: #2a2a2a;
    --card-dark: #1e1e20;
    --card-dark-2: #28282b;
    --edge-grey: #3a3a40;
    --gold-light: #e6c264;
    --gold-deep: #a8762c;
    --gold-text: #e2b24e;
    --ink-light: #ececec;
    --ink-mark: #2c2c31;
    --emboss: #141416;
  }
  * { box-sizing: border-box; margin: 0; padding: 0; }
  html, body { width: 1200px; height: 1138px; overflow: hidden; }
  body {
    background: var(--backdrop);
    font-family: "Roboto", Arial, sans-serif;
    position: relative;
  }
  .card {
    position: absolute;
    width: 620px;
    height: 375px;
    border-radius: 16px;
    overflow: hidden;
  }
  .card-front {
    left: 274px;
    top: 186px;
    width: 624px;
    height: 376px;
    background: linear-gradient(160deg, var(--card-dark) 0%, var(--card-dark-2) 100%);
  }
  .front-name {
    position: absolute;
    left: 0;
    right: 0;
    top: 212px;
    text-align: center;
    font-weight: 700;
    font-size: 40px;
    letter-spacing: 4px;
    text-transform: uppercase;
    color: var(--emboss);
  }
  .card-back {
    left: 276px;
    top: 608px;
    width: 618px;
    background: var(--card-dark);
  }
  .back-shape {
    position: absolute;
    inset: 0;
    width: 100%;
    height: 100%;
  }
  .contact-block {
    position: absolute;
    left: 31px;
    top: 86px;
    color: var(--ink-light);
  }
  .contact-name {
    font-weight: 500;
    font-size: 24px;
    color: var(--gold-text);
    line-height: 28px;
  }
  .contact-role {
    font-size: 16px;
    line-height: 24px;
    margin-bottom: 24px;
  }
  .contact-list { list-style: none; }
  .contact-list li {
    display: flex;
    align-items: center;
    gap: 16px;
    font-size: 17px;
    line-height: 24px;
  }
  .contact-list svg { width: 15px; height: 15px; fill: var(--gold-text); flex: none; }
  .contact-address {
    font-size: 17px;
    line-height: 24px;
    margin-top: 6px;
  }
  .back-name {
    position: absolute;
    left: 300px;
    width: 300px;
    top: 198px;
    text-align: center;
    font-weight: 700;
    font-size: 26px;
    letter-spacing: 2px;
    text-transform: uppercase;
    color: var(--ink-mark);
  }
</style>
</head>
<body>
  <section class="card card-front">
    <p class="front-name">Vale Crest</p>
  </section>

  <section class="card card-back">
    <svg class="back-shape" viewBox="0 0 618 375" preserveAspectRatio="none" aria-hidden="true">
      <defs>
        <linearGradient id="goldFill" x1="0" y1="0" x2="0" y2="1">
          <stop offset="0" stop-color="var(--gold-deep)"/>
          <stop offset="0.5" stop-color="var(--gold-light)"/>
          <stop offset="1" stop-color="var(--gold-deep)"/>
        </linearGradient>
      </defs>
      <path d="M319 0 C 238 70, 238 300, 322 375 L 337 375 C 250 300, 250 70, 343 0 Z" fill="var(--edge-grey)"/>
      <path d="M343 0 C 250 70, 250 300, 337 375 L 618 375 L 618 0 Z" fill="url(#goldFill)"/>
    </svg>

    <div class="contact-block">
      <p class="contact-name">Vale Crest</p>
      <p class="contact-role">Managing Director</p>
      <ul class="contact-list">
        <li>
          <svg viewBox="0 0 16 16"><path d="M2 5c0-2 2-3 6-3s6 1 6 3v1h-3V5H5v1H2zM4 7h8l2 6H2z"/></svg>
          828-555-0142
        </li>
        <li>
          <svg viewBox="0 0 16 16"><path d="M1 3h14v10H1zM2 4l6 5 6-5v1L8 10 2 5z" fill-rule="evenodd"/></svg>
          hello@valecrest.com
        </li>
        <li>
          <svg viewBox="0 0 16 16"><path d="M8 1a7 7 0 1 0 0 14A7 7 0 0 0 8 1zm0 1.5c1 1 1.6 2.7 1.7 4.5H6.3C6.4 5.2 7 3.5 8 2.5zM6.3 8h3.4c-.1 1.8-.7 3.5-1.7 4.5-1-1-1.6-2.7-1.7-4.5zM2.5 7h2.8c.1-1.6.5-3 1.1-4A5.5 5.5 0 0 0 2.5 7zm0 1a5.5 5.5 0 0 0 3.9 4c-.6-1-1-2.4-1.1-4zm8.2 0c-.1 1.6-.5 3-1.1 4a5.5 5.5 0 0 0 3.9-4zm0-1h2.8a5.5 5.5 0 0 0-3.9-4c.6 1 1 2.4 1.1 4z"/></svg>
          www.valecrest.com
        </li>
      </ul>
      <p class="contact-address">12 Harbor Lane, Westfield,<br>Oakridge, US 40217</p>
    </div>

    <p class="back-name">Vale Crest</p>
  </section>
</body>
</html>
```